Email Preference Page Design

We are looking for a 2 page design for our users to edit their email preferences and submit friend referrals. You can find the fuctionality, content and text here:

https://brightvanta.mailrelayhub.example/app/linkClick/7281/5fa9c1d3b07e442b/28374615/9bd4e01a7c3f2a65

* the shipping and billing address might be different so you need to show the billing if the "same as shipping" box is not checked. It can auto-hide like the page above shows if that fits your design.

* when the "unsubscribe from all email lists" box is selected, all the other checkbox options will hide as in the example page. We need you to show us what the site will look like with and without that checkbox selected.

We want to match these two pages to the general feel of these website pages:

www.brightvanta.com
and
free.brightvanta.com

The page should be very clean and tight. Project is for design only but must be able to be implemented in html showing button and checkbox states. Technically this must be two pages for our system - one for all the user info and one for individual email referrals (see example above).

Target Market(s)

video professionals

Industry/Entity Type

Shipping

Requirements
Must have
• our logo (see numerous versions attached)
well designed header
well designed sections
clean editable text
tight layout
html friendly
easy to understand
2 pages
Nice to have
• custom checkboxes and radio buttons

```html
<!DOCTYPE html>
<html lang="en">
<head>
<meta charset="utf-8">
<title>Communication Preferences – brightvanta</title>
<link href="https://fonts.googleapis.com/css2?family=Exo+2:wght@400;500;600&family=Open+Sans:ital,wght@0,400;0,600;0,700;1,400&display=swap" rel="stylesheet">
<style>
  :root{
    --navy:#1f2e3c;
    --orange:#f79c33;
    --orange-text:#f29a2e;
    --ink:#2b3540;
    --label:#4a4f55;
    --field-border:#d4d7da;
    --field-focus:#eef8fb;
    --white:#ffffff;
  }
  *{box-sizing:border-box;margin:0;padding:0}
  html,body{width:1200px;height:2532px;overflow:hidden}
  body{position:relative;background:var(--white);font-family:"Open Sans",Arial,sans-serif;color:var(--ink)}

  .top-bar{position:absolute;left:0;top:0;width:1200px;height:17px;background:var(--navy)}
  .brand-tab{position:absolute;left:287px;top:0;width:624px;height:149px;display:flex;align-items:center;justify-content:center;gap:18px}
  .brand-tab svg{position:absolute;inset:0}
  .brand-dot{position:relative;width:40px;height:40px;border-radius:50%;background:var(--orange)}
  .brand-name{position:relative;font-family:"Exo 2",sans-serif;font-weight:500;font-size:62px;color:var(--white);letter-spacing:1px;line-height:1}

  .page-title{position:absolute;left:0;top:205px;width:1200px;text-align:center;font-family:"Exo 2",sans-serif;font-weight:400;font-size:68px;color:var(--navy)}

  .required-tab{position:absolute;left:0;top:371px;width:30px;height:157px;background:var(--navy);border-radius:0 5px 5px 0;color:var(--white);font-size:15px;display:flex;align-items:center;justify-content:center}
  .required-tab span{transform:rotate(-90deg);white-space:nowrap}

  .section-head{position:absolute;font-size:30px;font-weight:600;color:var(--orange-text)}
  .rule{position:absolute;height:3px;background:var(--orange)}
  .rule::after{content:"";position:absolute;left:22px;top:3px;border-left:9px solid transparent;border-right:9px solid transparent;border-top:9px solid var(--orange)}
  .rule.light{background:var(--white);height:3px}
  .rule.light::after{border-top-color:var(--white)}

  .field-row{position:absolute;height:51px;display:flex;align-items:center}
  .field-label{font-size:21px;color:var(--label);text-align:right;padding-right:13px}
  .field{height:51px;border:2px solid var(--field-border);background:var(--white);font-size:21px;color:#555;display:flex;align-items:center;padding-left:14px;position:relative}
  .field.focus{background:var(--field-focus);border-color:#c2ccd2}
  .field.select::after{content:"";position:absolute;right:16px;top:20px;border-left:8px solid transparent;border-right:8px solid transparent;border-top:11px solid #9aa0a5}
  .field.select::before{content:"";position:absolute;right:44px;top:4px;bottom:4px;width:2px;background:var(--field-border)}
  .plus{width:39px;text-align:center;font-size:19px;color:var(--label)}

  .same-address{position:absolute;left:641px;top:450px;display:flex;gap:16px;font-size:29px;line-height:37px;color:var(--ink)}
  .same-address .box{width:24px;height:24px;border:2px solid #b8bdc2;background:var(--white);margin-top:8px;flex:none}

  .prefs{position:absolute;left:0;top:1219px;width:1200px;height:1282px;background:var(--orange);border-top:3px solid var(--navy)}
  .prefs-badge{position:absolute;left:556px;top:1174px;width:90px;height:90px;border-radius:50%;background:var(--navy);border:4px solid var(--white)}

  .check{position:absolute;display:flex;align-items:center;color:var(--white)}
  .check .box{width:24px;height:24px;background:var(--white);flex:none;border-radius:2px}
  .check.item{font-size:22px;gap:21px}
  .subscribe{left:52px;top:1342px;font-size:29px;font-weight:700;gap:14px}
  .subscribe-note{position:absolute;left:90px;top:1377px;font-size:27px;font-style:italic;color:var(--white)}
  .filter-note{position:absolute;left:51px;top:1432px;font-size:29px;font-weight:700;color:var(--white)}
  .col-head{position:absolute;font-size:29px;font-weight:600;line-height:31px;color:var(--white)}

  .unsubscribe{position:absolute;left:635px;top:2061px;width:509px;height:64px;background:var(--navy);display:flex;align-items:center;gap:16px;padding-left:18px;font-size:28px;font-weight:700;color:var(--white)}
  .unsubscribe .box{width:24px;height:24px;background:var(--white)}

  .submit{position:absolute;left:52px;top:2356px;width:361px;height:78px;background:var(--navy);border:2px solid #16212b;color:var(--white);font-size:38px;font-weight:600;display:flex;align-items:center;justify-content:center}

  .bottom-bar{position:absolute;left:0;top:2501px;width:1200px;height:31px;background:var(--navy)}
</style>
</head>
<body>
  <div class="top-bar"></div>
  <header class="brand-tab">
    <svg width="624" height="149" viewBox="0 0 624 149"><path d="M0 0H624V118Q624 132 610 136L480 149H144L14 136Q0 132 0 118Z" fill="#1f2e3c"/></svg>
    <span class="brand-dot"></span>
    <span class="brand-name">brightvanta</span>
  </header>

  <h1 class="page-title">Communication Preferences</h1>

  <div class="required-tab"><span>Required Fields*</span></div>

  <h2 class="section-head" style="left:51px;top:356px">Contact &amp; Billing</h2>
  <div class="rule" style="left:51px;top:406px;width:509px"></div>
  <h2 class="section-head" style="left:641px;top:356px">Shipping Address</h2>
  <div class="rule" style="left:641px;top:406px;width:507px"></div>

  <!-- contact & billing -->
  <div class="field-row" style="left:0;top:457px"><span class="field-label" style="width:214px">First Name*</span><span class="field focus" style="width:346px"></span></div>
  <div class="field-row" style="left:0;top:516px"><span class="field-label" style="width:214px">Last Name*</span><span class="field" style="width:346px"></span></div>
  <div class="field-row" style="left:0;top:575px"><span class="field-label" style="width:214px">Email*</span><span class="field" style="width:346px"></span></div>
  <div class="field-row" style="left:0;top:634px"><span class="field-label" style="width:214px">Phone</span><span class="field" style="width:346px"></span></div>
  <div class="field-row" style="left:0;top:692px"><span class="field-label" style="width:214px">Address 1</span><span class="field" style="width:346px"></span></div>
  <div class="field-row" style="left:0;top:752px"><span class="field-label" style="width:214px">Address 2</span><span class="field" style="width:346px"></span></div>
  <div class="field-row" style="left:0;top:813px"><span class="field-label" style="width:214px">Address 3</span><span class="field" style="width:346px"></span></div>
  <div class="field-row" style="left:0;top:871px"><span class="field-label" style="width:214px">City</span><span class="field" style="width:346px"></span></div>
  <div class="field-row" style="left:0;top:934px"><span class="field-label" style="width:214px">Select Country</span><span class="field select" style="width:346px"></span></div>
  <div class="field-row" style="left:0;top:991px"><span class="field-label" style="width:214px">State</span><span class="field" style="width:346px"></span></div>
  <div class="field-row" style="left:0;top:1061px"><span class="field-label" style="width:214px">Postal Code + 4</span><span class="field" style="width:139px">11111</span><span class="plus">+</span><span class="field" style="width:168px">1111</span></div>

  <!-- shipping -->
  <div class="same-address"><span class="box"></span><span>Billing address is same as<br>shipping address</span></div>
  <div class="field-row" style="left:600px;top:561px"><span class="field-label" style="width:215px">Street Address 1</span><span class="field" style="width:333px"></span></div>
  <div class="field-row" style="left:600px;top:621px"><span class="field-label" style="width:215px">Street Address 2</span><span class="field" style="width:333px"></span></div>
  <div class="field-row" style="left:600px;top:681px"><span class="field-label" style="width:215px">Street Address 3</span><span class="field" style="width:333px"></span></div>
  <div class="field-row" style="left:600px;top:739px"><span class="field-label" style="width:215px">City</span><span class="field" style="width:333px"></span></div>
  <div class="field-row" style="left:600px;top:801px"><span class="field-label" style="width:215px">Select Country</span><span class="field select" style="width:333px"></span></div>
  <div class="field-row" style="left:600px;top:859px"><span class="field-label" style="width:215px">State</span><span class="field" style="width:333px"></span></div>
  <div class="field-row" style="left:600px;top:919px"><span class="field-label" style="width:215px">Postal Code + 4</span><span class="field" style="width:140px">44444</span><span class="plus">+</span><span class="field" style="width:154px">2222</span></div>

  <!-- email preferences -->
  <section class="prefs"></section>
  <div class="prefs-badge"></div>

  <div class="check subscribe"><span class="box"></span>Subscribe me to your general email list</div>
  <p class="subscribe-note">This monthly email includes free video loops and VIP sale notices</p>
  <p class="filter-note">Help us filter our emails so we only sending relevant information to you</p>

  <div class="rule light" style="left:51px;top:1498px;width:510px"></div>
  <h3 class="col-head" style="left:51px;top:1512px">Send me emails about these<br>product types:</h3>
  <div class="rule light" style="left:51px;top:1591px;width:510px"></div>

  <div class="rule light" style="left:635px;top:1498px;width:510px"></div>
  <h3 class="col-head" style="left:635px;top:1512px">Send me emails about these<br>product types:</h3>
  <div class="rule light" style="left:635px;top:1591px;width:510px"></div>

  <div class="check item" style="left:51px;top:1630px"><span class="box"></span>Low energy motion loops</div>
  <div class="check item" style="left:51px;top:1677px"><span class="box"></span>High energy motion loops</div>
  <div class="check item" style="left:51px;top:1726px"><span class="box"></span>Timelapse footage</div>
  <div class="check item" style="left:51px;top:1778px"><span class="box"></span>Low energy motion loops</div>
  <div class="check item" style="left:51px;top:1833px"><span class="box"></span>High energy motion loops</div>
  <div class="check item" style="left:51px;top:1887px"><span class="box"></span>Timelapse footage</div>
  <div class="check item" style="left:51px;top:1942px"><span class="box"></span>Worship or wedding motion loops</div>
  <div class="check item" style="left:51px;top:1996px"><span class="box"></span>Pre-mixed DVDs and BluRay</div>
  <div class="check item" style="left:51px;top:2050px"><span class="box"></span>Entertainment lasers for concerts and clubs</div>
  <div class="check item" style="left:51px;top:2106px"><span class="box"></span>Entertainment lasers for text &amp; logo display</div>
  <div class="check item" style="left:51px;top:2160px"><span class="box"></span>Custom logo animation services</div>
  <div class="check item" style="left:51px;top:2214px"><span class="box"></span>Video software for creating video animations</div>
  <div class="check item" style="left:51px;top:2268px"><span class="box"></span>Video software for live performance (Vjing)</div>

  <div class="check item" style="left:635px;top:1630px"><span class="box"></span>VJing (live performance video)</div>
  <div class="check item" style="left:635px;top:1677px"><span class="box"></span>DJing (live performance audio+video)</div>
  <div class="check item" style="left:635px;top:1726px"><span class="box"></span>Performing in a band</div>
  <div class="check item" style="left:635px;top:1778px"><span class="box"></span>Video editing</div>
  <div class="check item" style="left:635px;top:1833px"><span class="box"></span>Corporate presentations</div>
  <div class="check item" style="left:635px;top:1887px"><span class="box"></span>Worship video services</div>
  <div class="check item" style="left:635px;top:1942px"><span class="box"></span>Lasers for entertainment &amp; branding</div>
  <div class="check item" style="left:635px;top:1996px"><span class="box"></span>Special offers from BrightVanta partners</div>

  <div class="unsubscribe"><span class="box"></span>Unsubscribe from all email lists</div>

  <div class="submit">Submit Now</div>

  <div class="bottom-bar"></div>
</body>
</html>
```